Letter design, envelope design, and more

Hello, we the Tavrin Gmbh are looking for our shop. Letter C5. Design does not have to be like a business card, so it can have straight lines. Only the color is important. The logo is the text under TaVRin omit.It should not be playful but Profesionel

Font styles to use
Sans Serif

Colors
0555a3
3176b5
85abd2
85cae6
34a7d8
0792cd
cee9f5
cfdfed
000000

Requirements
Must have
• Color like business card, Please, with the text under TaVRin, Correct address Lindmattstr. 4 Zip code 9517 Goldach, as well as Couvert Without addressing only design and logo with TaVrn
Nice to have
• more writing articles
Should not have
• Not too colored, Text under TaVRin, bright colors

```html
<!DOCTYPE html>
<html lang="de">
<head>
<meta charset="utf-8">
<title>Tavrin Gmbh – Briefpapier</title>
<link rel="stylesheet" href="https://fonts.googleapis.com/css2?family=Source+Sans+3:wght@400;700&display=swap">
<style>
  :root {
    --backdrop: #ececec;
    --paper: #ffffff;
    --brand-navy: #0555a3;
    --band-dark: #0f78c0;
    --band-light: #25a9e2;
    --mark-faint: #f2f4f8;
    --text-navy: #1d3a7a;
  }
  * { margin: 0; padding: 0; box-sizing: border-box; }
  html, body {
    width: 1200px;
    height: 900px;
    overflow: hidden;
    background: var(--backdrop);
    font-family: "Source Sans 3", Arial, sans-serif;
  }
  .letterhead {
    position: absolute;
    left: 290px;
    top: 50px;
    width: 620px;
    height: 800px;
    background: var(--paper);
    box-shadow: 0 6px 18px rgba(0, 0, 0, 0.18);
    overflow: hidden;
  }
  .letterhead__bands {
    position: absolute;
    inset: 0;
    width: 620px;
    height: 800px;
  }
  .band--light { fill: var(--band-light); }
  .band--dark { fill: var(--band-dark); }
  .brand {
    position: absolute;
    left: 58px;
    top: 138px;
    display: flex;
    align-items: center;
    gap: 10px;
  }
  .brand__square {
    width: 34px;
    height: 34px;
    background: var(--brand-navy);
  }
  .brand__name {
    font-weight: 700;
    font-size: 34px;
    letter-spacing: 1px;
    color: var(--brand-navy);
    line-height: 1;
  }
  .watermark {
    position: absolute;
    left: 0;
    right: 0;
    top: 330px;
    text-align: center;
    font-weight: 700;
    font-size: 120px;
    color: var(--mark-faint);
    line-height: 1;
  }
  .contact {
    position: absolute;
    left: 60px;
    top: 706px;
    font-size: 12.5px;
    line-height: 1.45;
    color: var(--text-navy);
  }
  .contact__line--indent { padding-left: 18px; }
</style>
</head>
<body>
  <main class="letterhead">
    <svg class="letterhead__bands" viewBox="0 0 620 800" aria-hidden="true">
      <polygon class="band--light" points="0,0 620,0 620,188 272,216 126,95 0,95"/>
      <polygon class="band--dark" points="0,0 126,95 0,95"/>
      <polygon class="band--dark" points="455,212 620,190 620,290"/>
      <polygon class="band--light" points="318,800 486,736 620,776 620,800"/>
    </svg>

    <div class="brand">
      <div class="brand__square"></div>
      <span class="brand__name">TaVRin</span>
    </div>

    <div class="watermark" aria-hidden="true">TaVRin</div>

    <address class="contact">
      <p class="contact__line">071 845 22 90 / Skype tavrin.office / info@tavrin-gmbh.ch</p>
      <p class="contact__line contact__line--indent">Lindmattstr. 4, 9517 Goldach</p>
    </address>
  </main>
</body>
</html>
```